Moravel Aesthetic Doctor

I require an elegant, luxurious looking business card for my aesthetic business. I am a doctor and that will set me aside from competitors. I am planning to provide home and spa based treatments to clients with high expectations. I have attached my logo.

```html
<!DOCTYPE html>
<html lang="en">
<head>
<meta charset="utf-8">
<title>Moravel Aesthetic Doctor – Business Card</title>
<link href="https://fonts.googleapis.com/css2?family=Raleway:wght@400;500;600&display=swap" rel="stylesheet">
<style>
  :root{
    --backdrop:#2d2e30;
    --card:#1d1e20;
    --sky:#52b4e9;
    --silver:#a6adbb;
    --white:#f4f6f8;
  }
  *{margin:0;padding:0;box-sizing:border-box}
  html,body{width:799px;height:1200px;overflow:hidden;background:var(--backdrop);font-family:"Raleway",Arial,sans-serif}
  .card{position:absolute;left:60px;width:680px;height:390px;background:var(--card);overflow:hidden;box-shadow:0 8px 24px rgba(0,0,0,.45)}
  .card--front{top:160px}
  .card--back{top:660px}

  .brand{position:absolute;display:flex;align-items:center;gap:16px}
  .brand__dot{width:70px;height:70px;border-radius:50%;background:var(--sky);flex:none}
  .brand__name{color:var(--silver);font-weight:500;letter-spacing:3px;text-transform:uppercase;line-height:1.15;white-space:nowrap}
  .brand__name .big{display:block;font-size:44px}
  .brand__name .small{display:block;font-size:20px;letter-spacing:4px}
  .card--front .brand{left:150px;top:40px}
  .card--back .brand{left:250px;top:196px}

  .services{position:absolute;left:0;right:0;top:182px;text-align:center;color:var(--white);font-size:19px;line-height:1.45}
  .band{position:absolute;left:0;right:0;top:262px;height:44px;background:var(--sky);color:var(--white);font-size:19px;letter-spacing:1px;text-align:center;line-height:44px;text-transform:uppercase}

  .wave{position:absolute;left:0;top:0}
  .tagline{position:absolute;left:26px;top:22px;color:var(--white);font-size:15px;line-height:1.25}
  .contact{position:absolute;left:34px;top:190px;color:var(--white);font-size:15px;line-height:1.7;list-style:none}
  .contact__follow{display:flex;align-items:center;gap:6px}
  .social{width:14px;height:14px;border-radius:50%;background:var(--sky);display:inline-block}
  .contact svg{width:12px;height:12px;margin-right:10px;vertical-align:-1px;fill:var(--sky)}
  .doctor{position:absolute;right:40px;top:282px;text-align:right}
  .doctor__name{color:var(--silver);font-size:26px;font-weight:400;line-height:1.1}
  .doctor__post{color:var(--sky);font-size:12px;font-style:italic;margin-top:2px}
  .doctor__cred{color:var(--sky);font-size:16px;font-weight:600;line-height:1.25;margin-top:4px}
</style>
</head>
<body>

<section class="card card--front" aria-label="Card front">
  <div class="brand">
    <span class="brand__dot"></span>
    <span class="brand__name"><span class="big">Moravel</span><span class="small">Aesthetic Doctor</span></span>
  </div>
  <p class="services">Dermal Injectables &nbsp;|&nbsp; Plasma Facials &nbsp;|&nbsp; Microneedling<br>Skin Boosters &nbsp;|&nbsp; Excessive Sweating</p>
  <div class="band">Home and Spa Based Treatments</div>
</section>

<section class="card card--back" aria-label="Card back">
  <svg class="wave" width="680" height="390" viewBox="0 0 680 390" aria-hidden="true">
    <path d="M0 0H680V150C560 110 420 115 330 110C200 104 90 75 0 95Z" fill="var(--sky)"/>
    <path d="M0 95C90 75 200 104 330 110C420 115 560 110 680 150V172C560 132 420 133 330 128C200 122 90 100 0 115Z" fill="var(--silver)"/>
  </svg>
  <p class="tagline">Home and Spa<br>Based Treatments</p>
  <ul class="contact">
    <li class="contact__follow">Follow us on: <span class="social"></span><span class="social"></span></li>
    <li><svg viewBox="0 0 24 24"><path d="M6.6 10.8a15.1 15.1 0 0 0 6.6 6.6l2.2-2.2c.3-.3.7-.4 1-.2 1.1.4 2.3.6 3.6.6.6 0 1 .4 1 1V20c0 .6-.4 1-1 1A17 17 0 0 1 3 4c0-.6.4-1 1-1h3.5c.6 0 1 .4 1 1 0 1.3.2 2.5.6 3.6.1.3 0 .7-.2 1z"/></svg>0800 555 014</li>
    <li><svg viewBox="0 0 24 24"><path d="M2 5h20v14H2zM4 7v.5l8 5 8-5V7l-8 5z"/></svg>lena@moravel.co.nz</li>
    <li><svg viewBox="0 0 24 24"><circle cx="12" cy="12" r="10"/></svg>www.moravel.co.nz</li>
  </ul>
  <div class="brand">
    <span class="brand__dot"></span>
    <span class="brand__name"><span class="big">Moravel</span><span class="small">Aesthetic Doctor</span></span>
  </div>
  <div class="doctor">
    <p class="doctor__name">Dr Lena Varga</p>
    <p class="doctor__post">MRCPCH MD</p>
    <p class="doctor__cred">Australasian Diploma of<br>Aesthetic Medicine</p>
  </div>
</section>

</body>
</html>
```